TL - business card

Tallow Partners is an insurance brokerage firm, inovative, proactive, vigorous, which aims to become the leader of the insurance brokers in Anfrica. We should like to get some designs which should be avoided also in Gray / Metallic for the Administration and Orange / Blue for the Managers (ike in the picture sent). The Blue / Green logo is not the correct one, but the source of the file. Please adjust the color accordingly for the business cards. 1 / Orange / Blue 2 / Gray / Metallic We want something classic but which is transmitted strenght, inovation, modernity and most of all, rapidity. We want something start-up like, very punchy and catching eye remaining profesional at the same time. Name: Dorian Whitlock Function: Managing Director Address: N ° 17/18 Rua Veloso - R / C 2B Direita - Bairro Mutamba - Luanda Tel: (+244) 947 582 316 Email: dorian.whitlock@tallow-p.example Website: www.tallow-p. example We want classic in the front and creative, colorfull at the back. The cards will be printed in relief, with very high quality of paper.
Insurance Broker
Colors
Designer to choose colors to be used in the design.

```html
<!DOCTYPE html>
<html lang="en">
<head>
<meta charset="utf-8">
<title>Tallow Partners – Business Card</title>
<link href="https://fonts.googleapis.com/css2?family=Roboto:wght@400;500;700&display=swap" rel="stylesheet">
<style>
  :root {
    --bg: #e4e5e7;
    --paper: #ffffff;
    --green: #0a9444;
    --blue: #29a8e0;
    --blue-soft: #d4ecf8;
    --ink: #555a5e;
    --shadow: rgba(0, 0, 0, 0.18);
  }
  * { margin: 0; padding: 0; box-sizing: border-box; }
  html, body {
    width: 1200px;
    height: 960px;
    overflow: hidden;
    background: var(--bg);
    font-family: "Roboto", Arial, sans-serif;
  }
  .canvas {
    width: 1200px;
    height: 960px;
    display: flex;
    flex-direction: column;
    align-items: center;
    justify-content: center;
    gap: 40px;
  }
  .card {
    position: relative;
    width: 760px;
    height: 434px;
    background: var(--paper);
    border-bottom: 6px solid var(--green);
    border-left: 4px solid var(--green);
    box-shadow: 0 12px 30px var(--shadow);
    overflow: hidden;
  }

  /* Back side */
  .card-back {
    display: flex;
    flex-direction: column;
    align-items: center;
    justify-content: center;
    gap: 22px;
  }
  .brand-mark {
    width: 110px;
    height: 110px;
    border-radius: 50%;
    background: var(--blue);
  }
  .brand-name {
    font-weight: 700;
    font-size: 52px;
    letter-spacing: 1px;
    color: var(--green);
    text-transform: uppercase;
    line-height: 1;
  }
  .back-web {
    font-size: 20px;
    letter-spacing: 9px;
    color: var(--ink);
  }

  /* Front side */
  .card-front .details {
    position: absolute;
    left: 60px;
    top: 66px;
    width: 380px;
  }
  .card-front .brand-name {
    font-size: 30px;
    margin-bottom: 46px;
  }
  .person-name {
    font-weight: 700;
    font-size: 28px;
    line-height: 1.2;
    color: var(--green);
  }
  .person-role {
    font-weight: 500;
    font-size: 19px;
    color: var(--blue);
    margin-bottom: 10px;
  }
  .address {
    font-size: 18px;
    line-height: 1.3;
    color: var(--ink);
    margin-bottom: 14px;
  }
  .contacts {
    list-style: none;
    font-size: 18px;
    line-height: 1.4;
    color: var(--ink);
  }
  .contacts li {
    display: flex;
    align-items: center;
    gap: 12px;
    white-space: nowrap;
  }
  .contacts svg { width: 16px; height: 16px; fill: var(--green); flex: none; }
  .front-mark {
    position: absolute;
    right: 56px;
    top: 56px;
    width: 310px;
    height: 310px;
    border-radius: 50%;
    background: var(--blue-soft);
  }
</style>
</head>
<body>
<main class="canvas">

  <section class="card card-back" aria-label="Card back">
    <span class="brand-mark" aria-hidden="true"></span>
    <p class="brand-name">Tallow Partners</p>
    <p class="back-web">www.tallow-p.example</p>
  </section>

  <section class="card card-front" aria-label="Card front">
    <div class="details">
      <p class="brand-name">Tallow Partners</p>
      <h1 class="person-name">Dorian Whitlock</h1>
      <p class="person-role">Managing Director</p>
      <p class="address">N ° 17/18 Rua Veloso<br>R / C 2B Direita<br>Bairro Mutamba, Luanda</p>
      <ul class="contacts">
        <li>
          <svg viewBox="0 0 24 24" aria-hidden="true"><path d="M6.6 10.8a15.1 15.1 0 0 0 6.6 6.6l2.2-2.2c.3-.3.7-.4 1-.2 1.1.4 2.3.6 3.6.6.6 0 1 .4 1 1V20c0 .6-.4 1-1 1C10.6 21 3 13.4 3 4c0-.6.4-1 1-1h3.5c.6 0 1 .4 1 1 0 1.3.2 2.5.6 3.6.1.3 0 .7-.2 1z"/></svg>
          (+244) 947 582 316
        </li>
        <li>
          <svg viewBox="0 0 24 24" aria-hidden="true"><path d="M2 5h20v14H2z M4 7v.4l8 5 8-5V7z" fill-rule="evenodd"/></svg>
          dorian.whitlock@tallow-p.example
        </li>
        <li>
          <svg viewBox="0 0 24 24" aria-hidden="true"><circle cx="12" cy="12" r="10"/></svg>
          www.tallow-p.example
        </li>
      </ul>
    </div>
    <span class="front-mark" aria-hidden="true"></span>
  </section>

</main>
</body>
</html>
```